Marble Orchard - Report on digital habits and attitudes

We are a research company and we have written a PowerPoint Report to present the results of a series of surveys conducted in the last three years. The research is about the "Marble Orchard": people are facing the opportunities and challanges of their lives transformed by the digital technologies. We have investigated a number of topics through thousands of interviews and we've analyzed the data presented in the PowerPoint document.
We're not quite satisfied with the look and feel of the report: it looks too flat and boring, too "basic" to be presented as a professional work, yet being just that. We'd like you to upgrade the graphics and style of the report up to the level of a professional research product. The document still needs to be fully editable (either text and charts) but you can rearrange all the contents as you please, adding images, changing font and text size, colors and whatever you think is necessary to reach our goal.

Target Market(s)

Media covering digital issues
Marketing executives
Public institutions and policy makers

Industry/Entity Type

Market Research

Requirements
Must have
• The treats of a professional work
Fully editable within PowerPoint (either text and charts)
Nice to have
• Smart images
Original organization of the pages
Colors and graphics coherent with the quillbrook.it logo/website look and feel
Should not have
• PPT document over 30 MBytes
Images violating copyright

```html
<!DOCTYPE html>
<html lang="it">
<head>
<meta charset="utf-8">
<title>Marble Orchard – Report</title>
<link href="https://fonts.googleapis.com/css2?family=Montserrat:wght@500;600;700;800&family=Roboto:wght@400&display=swap" rel="stylesheet">
<style>
:root{
  --ink:#2d2d3a;
  --body:#6b6b73;
  --sep:#c9cacd;
  --orange:#f08a2a;
  --coral:#ef6350;
  --red:#e8263f;
  --purple:#5e5b8e;
  --green:#6ca034;
  --blue:#2277b8;
  --teal:#3a9fa8;
  --sky:#3b8ec6;
  --navy:#34495e;
  --track:#d3d6e0;
  --gold:#e9b44c;
  --crimson:#a8174a;
  --grey:#8d8e93;
}
*{margin:0;padding:0;box-sizing:border-box}
html,body{width:1200px;height:4955px;overflow:hidden;background:#fff}
body{position:relative;font-family:"Roboto",Arial,sans-serif;color:var(--body)}
.abs{position:absolute}
.sep{position:absolute;left:0;width:1200px;height:14px;background:var(--sep)}
h1,h2{font-family:"Montserrat",sans-serif;font-weight:800;color:var(--ink);letter-spacing:1px}
h2{font-size:50px;line-height:1}
.rule{position:absolute;height:3px;width:46px;background:var(--orange)}
.copy{font-size:11.5px;line-height:27px;text-align:justify}
.brand-mini{position:absolute;right:26px;display:flex;align-items:center;gap:6px;font-family:"Montserrat",sans-serif;font-weight:700;font-size:13px;color:var(--orange)}
.brand-mini i{display:block;width:14px;height:14px;border-radius:50%;background:var(--orange)}

/* hero */
.hero{position:absolute;left:0;top:0;width:1200px;height:790px;
  background:linear-gradient(135deg,var(--gold) 0%,#e0793a 35%,#c63a45 65%,var(--crimson) 100%)}
.hero .glow{position:absolute;left:360px;top:40px;width:520px;height:640px;border-radius:50%;
  background:radial-gradient(circle,rgba(255,255,255,.16),rgba(255,255,255,0) 70%)}
.hero .mark{position:absolute;left:560px;top:190px;width:80px;height:80px;border-radius:50%;border:13px solid #fff}
.hero h1{position:absolute;left:0;top:420px;width:1200px;text-align:center;color:#fff;font-size:98px;letter-spacing:2px}

/* intro */
.photo{position:absolute;border:6px solid #fff;box-shadow:0 0 0 1px #ddd}
.intro h2{position:absolute;left:708px;top:880px;font-size:52px}
.intro .copy{position:absolute;left:708px;width:415px}

/* research */
.center-title{position:absolute;left:0;width:1200px;text-align:center}
.topic{position:absolute;left:628px;display:flex;align-items:center;gap:20px;font-family:"Montserrat",sans-serif;font-weight:600;font-size:16px;color:var(--ink)}
.topic .dot{width:82px;height:82px;border-radius:50%;display:flex;align-items:center;justify-content:center}

/* fears */
.bar-label{position:absolute;right:104px;font-family:"Montserrat",sans-serif;font-weight:600;font-size:16px}

/* hopes */
.chart{position:absolute;left:77px;top:3648px;width:1048px;height:506px;border:1px solid #e3e3e3}
.chart-head{height:48px;background:var(--orange);color:#fff;font-family:"Montserrat",sans-serif;font-weight:600;font-size:14px;line-height:48px;text-align:center}

/* thanks */
.thanks{position:absolute;left:0;top:4212px;width:1200px;height:743px;
  background:radial-gradient(ellipse at 50% 55%,#a2a3a8 0%,var(--grey) 55%,#7d7e83 100%)}
.thanks .mark{position:absolute;left:560px;top:180px;width:80px;height:80px;border-radius:50%;border:13px solid #fff}
.thanks h1{position:absolute;left:0;top:395px;width:1200px;text-align:center;color:#fff;font-size:104px;letter-spacing:3px}
</style>
</head>
<body>

<!-- Hero -->
<section class="hero" role="img" aria-label="Fotografia di mani che sorreggono un globo digitale luminoso, con filtro arancio e cremisi">
  <div class="glow"></div>
  <div class="mark"></div>
  <h1>MARBLE ORCHARD</h1>
</section>
<div class="sep" style="top:790px"></div>

<!-- Introduzione -->
<section class="intro">
  <div class="brand-mini" style="top:830px"><i></i>Marble Orchard</div>
  <div class="photo" role="img" aria-label="Uomo d'affari seduto su una panchina che usa un tablet" style="left:79px;top:932px;width:286px;height:358px;background:linear-gradient(160deg,#c9d0d6,#6f6258 60%,#3b3430)"></div>
  <div class="photo" role="img" aria-label="Dettaglio di tablet e bicicletta in città" style="left:396px;top:963px;width:244px;height:239px;background:linear-gradient(150deg,#8a9094,#4e5559 55%,#2c3033)"></div>
  <div class="photo" role="img" aria-label="Mani che scrivono su un tablet, panchina in legno" style="left:240px;top:1204px;width:275px;height:230px;background:linear-gradient(170deg,#b9b2a6,#7c6650 60%,#4a3a2c)"></div>
  <h2>INTRODUZIONE</h2>
  <p class="copy" style="top:953px">Il digitale ha cambiato il mondo a un livello di profondità di cui non siamo ancora pienamente consapevoli. E' facile riconoscere le manifestazioni del digitale nei comportamenti delle persone e notare come ha formato nuove abitudini e ritualità quotidiane.Non è altrettanto immediato comprendere quanto il digitale abbia modificato il mondo interiore e abbia inciso sul senso dell'identità, sulle emozioni in gioco nelle relazioni, su affetti e sessualità, sul modo di concepire la società, i diritti e la libertà personale.</p>
  <p class="copy" style="top:1160px">L'obiettivo di questo lavoro di ricerca è raccontare la struttura e l'evoluzione di alcuni atteggiamenti di fondo che influenzano i comportamenti quotidiani legati alle tecnologie digitali. Le informazioni sono ricavate dalle dichiarazioni di campioni di individui chiamati a riflettere sull'ambiente connesso, cioè l'insieme di tutte le relazioni e attività che si possono svolgere grazie alla Rete e, più in generale, grazie a tutte le innovazioni introdotte dagli strumenti e dai servizi digitali.</p>
  <p class="copy" style="top:1347px">L'analisi indaga le dinamiche cognitive e psicologiche che originano i comportamenti e descrive gli orientamenti di base sottostanti alle scelte – talvolta inconsapevoli – che danno forma alla dimensione digitale della vita. Questa, infatti, può assumere una configurazione molto diversa dalla dimensione della vita di prima</p>
</section>
<div class="sep" style="top:1538px"></div>

<!-- La ricerca -->
<section class="research">
  <div class="brand-mini" style="top:1580px"><i></i>Marble Orchard</div>
  <h2 class="center-title" style="top:1600px">LA RICERCA</h2>
  <div class="rule" style="left:577px;top:1664px"></div>
  <p class="copy abs" style="left:88px;top:1705px;width:484px">L'ambiente connesso è tutto ciò che accade perché siamo connessi alla rete: tutti i modi che, grazie alla connessione alla rete, abbiamo per comunicare con altre persone e tessere relazioni, per fruire di contenuti di tutti i tipi (informazioni testuali, video, musica, giochi etc), per acquistare prodotti e utilizzare servizi (bancari, amministrativi, pagamenti), o utilizzare nuove tecnologie per la casa, per la mobilità, per il fitness e la salute, etc....Alcune di queste attività fanno ormai parte della nostra vita quotidiana, altre probabilmente lo diventeranno nei prossimi anni.</p>
  <p class="copy abs" style="left:635px;top:1705px;width:483px">La popolazione online riesce quindi a rappresentare quella fetta di società italiana maggiormente impattata dal fenomeno della digitalizzazione e del mondo connesso, anche se con livelli di consapevolezza, stress, paure e atteggiamenti completamente diversi che descrivono «mondi» molto diversi.La popolazione online riesce quindi a rappresentare quella fetta di società italiana maggiormente impattata dal fenomeno della digitalizzazione e del mondo connesso, anche se con livelli di consapevolezza, completamente diversi che descrivono «mondi» molto diversi.</p>

  <svg class="abs" style="left:101px;top:1972px" width="440" height="440" viewBox="0 0 440 440" aria-label="Grafico ad anelli delle aree tematiche">
    <g fill="none" stroke-width="15">
      <circle cx="220" cy="220" r="206" stroke="var(--track)"/>
      <circle cx="220" cy="220" r="177" stroke="var(--track)"/>
      <circle cx="220" cy="220" r="148" stroke="var(--track)"/>
      <circle cx="220" cy="220" r="121" stroke="var(--track)"/>
      <circle cx="220" cy="220" r="96" stroke="var(--track)"/>
      <path d="M14 220 A206 206 0 0 1 398 117" stroke="var(--red)"/>
      <path d="M43 220 A177 177 0 0 1 394 189" stroke="var(--purple)"/>
      <path d="M72 220 A148 148 0 0 1 368 220" stroke="var(--orange)"/>
      <path d="M99 220 A121 121 0 0 1 340 231" stroke="var(--green)"/>
      <path d="M124 220 A96 96 0 0 1 310 253" stroke="var(--blue)"/>
    </g>
    <circle cx="220" cy="220" r="9" fill="var(--orange)"/>
    <text x="220" y="246" text-anchor="middle" font-family="Montserrat,sans-serif" font-weight="700" font-size="11" fill="var(--orange)">Marble Orchard</text>
  </svg>

  <div class="topic" style="top:1949px"><span class="dot" style="background:var(--red)"><svg width="34" height="34" viewBox="0 0 24 24" fill="none" stroke="#fff" stroke-width="2" stroke-linejoin="round"><path d="M22 2 2 10l8 3 3 8z"/><path d="M22 2 10 13"/></svg></span>8 Domande sulle paure</div>
  <div class="topic" style="top:2041px"><span class="dot" style="background:var(--purple)"><svg width="34" height="34" viewBox="0 0 24 24" fill="none" stroke="#fff" stroke-width="2.4" stroke-linecap="round"><circle cx="10.5" cy="10.5" r="6"/><path d="m15 15 5 5"/></svg></span>8 Domande sulle speranze</div>
  <div class="topic" style="top:2132px"><span class="dot" style="background:var(--orange)"><svg width="30" height="30" viewBox="0 0 24 24" fill="#fff"><path d="M12 2l2 3 3.5-1 .5 3.5 3.5 1-1 3.5 2 2-3 2 1 3.5-3.5.5-1 3.5-3.5-1L12 22l-2-3-3.5 1-.5-3.5-3.5-1 1-3.5-2-2 3-2-1-3.5 3.5-.5 1-3.5 3.5 1z"/><circle cx="12" cy="12" r="3.5" fill="var(--orange)"/></svg></span>7 di atteggiamento</div>
  <div class="topic" style="top:2224px"><span class="dot" style="background:var(--green)"><svg width="32" height="32" viewBox="0 0 24 24" fill="none" stroke="#fff" stroke-width="2.2" stroke-linecap="round"><path d="M14 4l6 6M17 7l-10 10-4 4M7 17l-2-2 10-10"/></svg></span>7 su Data&amp;privacy</div>
  <div class="topic" style="top:2315px"><span class="dot" style="background:var(--blue)"><svg width="34" height="34" viewBox="0 0 24 24" fill="none" stroke="#fff" stroke-width="2" stroke-linejoin="round"><path d="M4 13l4-2 4 2v5l-4 2-4-2zM12 13l4-2 4 2v5l-4 2-4-2zM8 6l4-2 4 2v5l-4 2-4-2z"/></svg></span>7 sulla societa digitale</div>
</section>
<div class="sep" style="top:2462px"></div>

<!-- Le paure -->
<section class="fears">
  <h2 class="abs" style="left:40px;top:2566px">LE PAURE</h2>
  <div class="rule" style="left:42px;top:2627px"></div>
  <p class="copy abs" style="left:42px;top:2660px;width:486px">Il digitale può fare paura per le conseguenze che produce nelle capacità cognitive, nelle relazioni personali e sociali, fino a quelle internazionali. Molti non conoscono cosa c'è dietro e da dove vengono certe magie della tecnologia, alle quali ci siamo abituati e che non ci meravigliano più ma rimangono in gran parte incomprensibili. Inoltre, certi racconti sulle sorveglianza digitale e sui nuovi poteri che emergono dai dati ispirano un senso di sospetto condiviso da un'ampia maggioranza di individui.</p>
  <p class="copy abs" style="left:42px;top:2845px;width:486px">Il sospetto che il flusso di informazioni generato dalle tecnologie sia utilizzato con finalità di controllo o manipolazione è molto diffuso e riguarda otto individui sui dieci.Il 77% si dichiara d'accordo con l'affermazione secondo la quale il digitale crea problemi di socialità nei ragazzi e il dato aumenta tra le</p>
  <p class="copy abs" style="left:42px;top:2985px;width:1061px">persone oltre i 54 anni di età. Così come tra i meno giovani trova conferma l'idea, già piuttosto diffusa, che il digitale diminuisca le capacità di apprendimento.Le paure sulle conseguenze politiche e sociali del digitale sono più contenute ma riguardano pur sempre un terzo della popolazione.Il sospetto che il flusso di informazioni generato dalle tecnologie sia utilizzato con finalità di controllo o manipolazione è molto diffuso e riguarda otto individui sui dieci. Il 77% si dichiara d'accordo con l'affermazione secondo la quale il digitale crea problemi di socialità nei ragazzi e il dato aumenta tra le giovani trova conferma l'idea, già piuttosto diffusa, che il digitale</p>

  <span class="bar-label" style="top:2577px;color:var(--orange)">33%</span>
  <span class="bar-label" style="top:2635px;color:var(--coral)">35%</span>
  <span class="bar-label" style="top:2696px;color:var(--teal)">42%</span>
  <span class="bar-label" style="top:2758px;color:var(--sky)">70%</span>
  <span class="bar-label" style="top:2819px;color:var(--red)">80%</span>
  <span class="bar-label" style="top:2885px;color:var(--navy)">100%</span>
  <svg class="abs" style="left:650px;top:2590px" width="450" height="360" aria-label="Barre percentuali delle paure">
    <g stroke-width="14">
      <line x1="19" y1="25" x2="333" y2="25" stroke="var(--track)"/><line x1="333" y1="25" x2="446" y2="25" stroke="var(--orange)"/>
      <line x1="19" y1="83" x2="302" y2="83" stroke="var(--track)"/><line x1="302" y1="83" x2="446" y2="83" stroke="var(--coral)"/>
      <line x1="19" y1="144" x2="265" y2="144" stroke="var(--track)"/><line x1="265" y1="144" x2="446" y2="144" stroke="var(--teal)"/>
      <line x1="19" y1="206" x2="196" y2="206" stroke="var(--track)"/><line x1="196" y1="206" x2="446" y2="206" stroke="var(--sky)"/>
      <line x1="19" y1="267" x2="108" y2="267" stroke="var(--track)"/><line x1="108" y1="267" x2="446" y2="267" stroke="var(--red)"/>
      <line x1="31" y1="333" x2="446" y2="333" stroke="var(--navy)"/>
    </g>
    <g fill="#fff" stroke-width="6">
      <circle cx="333" cy="25" r="14" stroke="var(--orange)"/>
      <circle cx="302" cy="83" r="14" stroke="var(--coral)"/>
      <circle cx="265" cy="144" r="14" stroke="var(--teal)"/>
      <circle cx="196" cy="206" r="14" stroke="var(--sky)"/>
      <circle cx="108" cy="267" r="14" stroke="var(--red)"/>
      <circle cx="31" cy="333" r="14" stroke="var(--navy)"/>
    </g>
  </svg>
</section>
<div class="sep" style="top:3154px"></div>

<!-- Le speranze -->
<section class="hopes">
  <h2 class="center-title" style="top:3222px">LE SPERANZE</h2>
  <div class="rule" style="left:577px;top:3290px"></div>
  <p class="copy abs" style="left:188px;top:3314px;width:824px;text-align:center">Un italiano su due guarda alla diffusione del digitale con un atteggiamento positivo, fiducioso nel fatto che questo fenomeno possa avere un impatto virtuoso su diversi ambiti della vita quotidiana dei cittadini e sulla società. La speranza più diffusa è la semplificazione conseguente al processo di digitalizzazione: il 77% del campione ritiene che il processo di digitalizzazione rende più semplice la vita dei cittadini. Attorno e grazie al digitale si sviluppano inoltre competenze e una generale crescita di conoscenza di cui beneficia tutta la società.</p>
  <p class="copy abs" style="left:188px;top:3452px;width:824px;text-align:center">La maggioranza dei cittadini ripone una grande fiducia nelle smart technologies che ci si aspetta siano in grado di rendere gli ambienti in cui viviamo (case, città, uffici) dei luoghi migliori, dove vivere con una qualità più elevata. Il tema dell'informazione online, invece, divide la popolazione tra chi ritiene che la diffusione dell'informazione online abbia un impatto positivo sul sistema informativo e chi non vede un miglioramento della qualità e della trasparenza dell'informazione. Meno diffuse sono le aspettative riposte negli effetti positivi delle tecnologie digitali in ambito sanitario, sul funzionamento del sistema democratico e sull'emersione del «nero».</p>

  <div class="chart">
    <div class="chart-head">Il trend dell'indice di speranza</div>
    <svg width="1046" height="456" viewBox="0 0 1046 456" aria-label="Grafico a linea dell'indice di speranza">
      <g fill="none" stroke="var(--sky)" stroke-width="1.5"><rect x="32" y="44" width="4" height="8"/><rect x="38" y="40" width="4" height="12"/><rect x="44" y="34" width="4" height="18"/><line x1="30" y1="52" x2="50" y2="52"/></g>
      <text x="63" y="52" font-family="Roboto,sans-serif" font-size="13" fill="#555">13/01/2021 - 20/08/2021</text>
      <g stroke="#e6e6e6" stroke-width="1">
        <line x1="135" y1="123" x2="1010" y2="123"/><line x1="135" y1="177" x2="1010" y2="177"/>
        <line x1="135" y1="229" x2="1010" y2="229"/><line x1="135" y1="283" x2="1010" y2="283"/>
        <line x1="135" y1="336" x2="1010" y2="336"/><line x1="135" y1="390" x2="1010" y2="390" stroke="#ccc"/>
      </g>
      <g font-family="Roboto,sans-serif" font-size="9" fill="#666" text-anchor="end">
        <text x="125" y="126">1.25</text><text x="125" y="180">1</text><text x="125" y="232">0.75</text>
        <text x="125" y="286">0.5</text><text x="125" y="339">0.25</text><text x="125" y="393">0</text>
      </g>
      <g stroke="#666" stroke-width="1.5"><line x1="83" y1="119" x2="93" y2="119"/><line x1="83" y1="123" x2="93" y2="123"/><line x1="83" y1="127" x2="93" y2="127"/></g>
      <text transform="translate(58 260) rotate(-90)" text-anchor="middle" font-family="Roboto,sans-serif" font-size="11" fill="#666">Number</text>
      <g font-family="Roboto,sans-serif" font-size="9" fill="#666" text-anchor="middle">
        <text x="183" y="410">12/27/2020</text><text x="292" y="410">12/28/2020</text><text x="402" y="410">12/29/2020</text>
        <text x="511" y="410">12/30/2020</text><text x="621" y="410">12/31/2020</text><text x="731" y="410">01/01/2021</text>
        <text x="840" y="410">01/02/2021</text><text x="950" y="410">01/03/2021</text>
      </g>
      <path d="M256 242 C330 290 360 315 413 306 C470 296 520 210 573 206 C630 195 690 195 734 200 C800 204 850 210 894 221" fill="none" stroke="#8a7d2a" stroke-width="2" stroke-dasharray="2 4"/>
      <g fill="var(--orange)">
        <circle cx="256" cy="242" r="7"/><circle cx="413" cy="306" r="7"/><circle cx="573" cy="206" r="7"/>
        <circle cx="734" cy="200" r="7"/><circle cx="894" cy="221" r="7"/>
      </g>
      <g font-family="Roboto,sans-serif" font-size="16" fill="#666" text-anchor="middle">
        <text x="256" y="270">53%</text><text x="413" y="334">51%</text><text x="573" y="234">54%</text>
        <text x="734" y="228">55%</text><text x="894" y="249">54%</text>
      </g>
    </svg>
  </div>
</section>

<!-- Thank you -->
<section class="thanks" role="img" aria-label="Fotografia in scala di grigi di una persona di spalle davanti a un paesaggio urbano digitale">
  <div class="mark"></div>
  <h1>THANK YOU</h1>
</section>

</body>
</html>
```